Flyer informing about the activities of people in action

Leute im Wandel (www.leuteimwandel.ch) offers coaching, medation, support for traumatized people and conflict and crisis intervention. The flyer should inform about the activities in a plain and simple way (see logo on the homepage).

Target Market(s)

Adults who live in Switzerland or Germany

Requirements
Must have
• - simple flyer, the design is based on my logo. Brief information about my offer, reference to my homepage www.leuteimwandel.
- 2-sided: on the first page - fire circle with text (see homepage - Home), on the back - offer with logo
- possibly a square flyer

Should not have
• no photos

```html
<!DOCTYPE html>
<html lang="de">
<head>
<meta charset="utf-8">
<title>Angebot – Coaching, Begleitung, Mediation</title>
<link rel="stylesheet" href="https://fonts.googleapis.com/css2?family=Allura&family=Questrial&display=swap">
<style>
  :root {
    --ochre: #9a7a2e;
    --ink: #ffffff;
    --gold: #e9c545;
    --gold-deep: #c99d2a;
  }
  * { margin: 0; padding: 0; box-sizing: border-box; }
  html, body {
    width: 1200px;
    height: 1200px;
    overflow: hidden;
    background: var(--ochre);
  }
  .flyer-back {
    position: relative;
    width: 1200px;
    height: 1200px;
    overflow: hidden;
    background: var(--ochre);
    color: var(--ink);
    font-family: "Questrial", "Helvetica Neue", Arial, sans-serif;
  }
  .headline {
    position: absolute;
    left: 0;
    top: 218px;
    width: 1200px;
    text-align: center;
    font-family: "Allura", cursive;
    font-size: 90px;
    line-height: 1;
    font-weight: 400;
    white-space: nowrap;
  }
  .subline {
    position: absolute;
    left: 0;
    top: 381px;
    width: 1200px;
    text-align: center;
    font-size: 35px;
    letter-spacing: 0.13em;
    text-transform: uppercase;
    line-height: 1;
    white-space: nowrap;
  }
  .offer-list {
    position: absolute;
    left: 118px;
    top: 524px;
    list-style: none;
  }
  .offer {
    position: relative;
    padding-left: 79px;
    height: 187px;
  }
  .offer-bullet {
    position: absolute;
    left: 0;
    top: 1px;
    width: 38px;
    height: 38px;
  }
  .offer-title {
    font-size: 34px;
    letter-spacing: 0.08em;
    text-transform: uppercase;
    font-weight: 400;
    line-height: 40px;
  }
  .offer-text {
    margin-top: 11px;
    font-size: 37px;
    letter-spacing: 0.02em;
    line-height: 41px;
    width: 960px;
    white-space: nowrap;
  }
</style>
</head>
<body>
  <main class="flyer-back">
    <h1 class="headline">Ich begleite Sie und bringe Ihnen</h1>
    <p class="subline">Orientierung, Klarheit &amp; Unterstützung</p>

    <ul class="offer-list">
      <li class="offer">
        <svg class="offer-bullet" viewBox="0 0 42 42" aria-hidden="true">
          <circle cx="21" cy="21" r="17" fill="none" stroke="var(--gold)" stroke-width="3"/>
          <circle cx="21" cy="21" r="11" fill="none" stroke="var(--gold-deep)" stroke-width="2"/>
        </svg>
        <h2 class="offer-title">Coaching</h2>
        <p class="offer-text">Manchmal brauchen Sie ein Gegenüber zum Klären<br>Ihrer Situation.</p>
      </li>
      <li class="offer">
        <svg class="offer-bullet" viewBox="0 0 42 42" aria-hidden="true">
          <circle cx="21" cy="21" r="17" fill="none" stroke="var(--gold)" stroke-width="3"/>
          <circle cx="21" cy="21" r="11" fill="none" stroke="var(--gold-deep)" stroke-width="2"/>
        </svg>
        <h2 class="offer-title">Begleitung</h2>
        <p class="offer-text">Manchmal brauchen Sie jemanden, bei dem Sie sich<br>sicher fühlen.</p>
      </li>
      <li class="offer">
        <svg class="offer-bullet" viewBox="0 0 42 42" aria-hidden="true">
          <circle cx="21" cy="21" r="17" fill="none" stroke="var(--gold)" stroke-width="3"/>
          <circle cx="21" cy="21" r="11" fill="none" stroke="var(--gold-deep)" stroke-width="2"/>
        </svg>
        <h2 class="offer-title">Mediation</h2>
        <p class="offer-text">Manchmal brauchen Sie eine Brückenbauerin für<br>neue Begegnungen.</p>
      </li>
    </ul>
  </main>
</body>
</html>
```